Kestrel Baseball & Softball Camp 2017

Design a flyer that will promote our 2017 summer camp for boys and girls softball.

Weeks of
July 10th - 14th
July 17th - 21st.

Players ages 5 - 11.
Full day = 9:30am - 2:30pm half day = 9:30am - 11:30am.
$295 / full day : $195/ half day

Hosted by "Kestrel Baseball" affiliated with the Harbor Comets Travel Baseball & Softball Club and the Maple Ridge Youth League,

Camp Location MRYL, Route 9C Birch Hollow.

PHone 555-240-7813, email info@kestrelball.example

The color should be "Red white and blue color scheme" with dates and location standing out. Kestrel Logo should be prominent MRYL and Comets smaller and secondary.

Feel free to use stock photo's if available. visit www.harborcomets.example for more pictures and there are links for the 2017 summer camp there with possibly some more information.

Target Market(s)

to catch the eye of parents of players ages 5 - 11 already at little league or shopping in local stores

Colors
ec1f27
0355a3
ffffff

Requirements
Must have
• red white and blue design,
• Kestrel logo and summer camp prominent so it catches the eye and explains what it is right away.
• the comets and maple ridge logo's a the bottom showing the affiliation.
Nice to have
• stock photo's or something showing players having a great time or a beautiful ballpark
Should not have
• to much clutter or hard to figure out what it's for

```html
<!DOCTYPE html>
<html lang="en">
<head>
<meta charset="utf-8">
<title>Kestrel Baseball &amp; Softball Summer Camp 2017</title>
<link href="https://fonts.googleapis.com/css2?family=Oswald:wght@500;600;700&family=Kaushan+Script&family=Montserrat:wght@600;800&display=swap" rel="stylesheet">
<style>
:root{
  --red:#e0202a;
  --navy:#1f3a6e;
  --blue:#0355a3;
  --white:#ffffff;
  --sky-top:#dcebf6;
  --sky-low:#7f9cc0;
  --dirt-top:#b8957b;
  --dirt-low:#93735c;
}
*{margin:0;padding:0;box-sizing:border-box}
html,body{width:819px;height:1200px;overflow:hidden;background:var(--white)}
.flyer{position:relative;width:819px;height:1200px;overflow:hidden;background:var(--white);font-family:'Oswald',sans-serif;color:var(--navy)}
.abs{position:absolute}
.hero-photo{left:0;top:0;width:819px;height:500px;background:linear-gradient(180deg,var(--sky-top) 0%,#b9cfe4 45%,var(--sky-low) 100%)}
.field-photo{left:0;top:440px;width:819px;height:420px;background:linear-gradient(180deg,var(--dirt-top) 0%,#a5846b 60%,var(--dirt-low) 100%)}
.swoosh{left:0;width:819px}
.brand-badge{left:540px;top:250px;width:200px;height:200px;border-radius:50%;background:var(--white);border:6px solid var(--red);box-shadow:0 0 0 6px var(--white);display:flex;flex-direction:column;align-items:center;justify-content:center;color:var(--red);font-weight:700;line-height:1;text-align:center}
.brand-badge .name{font-size:44px}
.brand-badge .sub{font-size:20px;letter-spacing:1px;margin-top:6px}
.sport{left:72px;top:522px;font-family:'Montserrat',sans-serif;font-weight:800;font-size:32px;letter-spacing:11px;color:var(--white)}
.summer{left:34px;top:548px;font-family:'Kaushan Script',cursive;font-size:112px;line-height:1;color:var(--white)}
.camp{left:452px;top:530px;font-size:112px;font-weight:700;line-height:1.1;color:var(--navy)}
.year{left:740px;top:585px;font-size:46px;font-weight:700;color:var(--navy);transform:rotate(-90deg);transform-origin:left top}
.audience{left:500px;top:650px;font-family:'Kaushan Script',cursive;font-size:34px;color:var(--navy)}
.rule{left:80px;top:666px;width:410px;height:2px;background:var(--white)}
.weeks-label{left:96px;top:666px;font-family:'Kaushan Script',cursive;font-size:28px;line-height:36px;color:var(--navy)}
.dates{left:92px;top:700px;list-style:none}
.dates li{font-size:36px;font-weight:600;line-height:44px;color:var(--navy);display:flex;align-items:center}
.dates li::before{content:"";width:0;height:0;border-top:8px solid transparent;border-bottom:8px solid transparent;border-left:12px solid var(--red);margin-right:10px}
.ages-icon{left:470px;top:818px}
.ages-label{left:518px;top:810px;font-size:30px;font-weight:600;line-height:36px;color:var(--navy)}
.ages-range{left:645px;top:780px;width:130px;height:130px;border-radius:50%;background:var(--navy);color:var(--white);font-size:40px;font-weight:600;display:flex;align-items:center;justify-content:center}
.schedule{left:70px;top:936px}
.schedule .row{display:flex;align-items:center;font-size:27px;font-weight:600;line-height:38px;color:var(--navy)}
.schedule .row.indent{padding-left:50px}
.schedule svg{margin-right:14px}
.cost-label{left:462px;top:940px;font-family:'Kaushan Script',cursive;font-size:30px;color:var(--navy)}
.cost-icon{left:526px;top:944px;width:38px;height:38px;border-radius:50%;background:var(--red);color:var(--white);font-weight:700;font-size:24px;display:flex;align-items:center;justify-content:center}
.prices{left:578px;top:930px;font-size:27px;font-weight:600;line-height:36px;color:var(--navy)}
.info-bar{left:40px;top:1040px;width:739px;height:140px;border-top:2px dashed var(--navy);border-bottom:2px dashed var(--navy)}
.hosted{left:56px;top:1060px;width:290px;font-family:'Montserrat',sans-serif;font-weight:800;font-size:10.5px;line-height:16px;color:var(--navy);text-transform:uppercase}
.partners{left:56px;top:1130px;display:flex;gap:22px;align-items:center}
.partner{display:flex;align-items:center;gap:6px;font-size:18px;font-weight:600;color:var(--red)}
.partner.alt{color:var(--navy)}
.partner i{display:block;width:14px;height:14px;background:currentColor}
.location{left:370px;top:1062px}
.contact{left:568px;top:1062px}
.block-title{display:flex;align-items:center;gap:10px;font-family:'Kaushan Script',cursive;font-size:22px;color:var(--navy)}
.block-text{margin-top:8px;padding-left:28px;font-size:17px;font-weight:500;line-height:24px;color:var(--navy);text-transform:uppercase}
.contact .block-text{font-size:15.5px}
.contact .lower{text-transform:none}
</style>
</head>
<body>
<main class="flyer">
  <div class="abs hero-photo" role="img" aria-label="Three smiling young ball players in uniforms and a catcher's helmet against a bright sky"></div>
  <div class="abs field-photo" role="img" aria-label="Close view of an infield dirt baseline with a white chalk line"></div>

  <svg class="abs swoosh" style="top:400px" width="819" height="110" viewBox="0 0 819 110" aria-hidden="true">
    <path d="M0 30 C220 70 520 40 819 0 L819 40 C560 80 260 100 0 90 Z" fill="var(--navy)"/>
    <path d="M0 70 C250 110 560 70 819 30 L819 55 C560 95 260 110 0 110 Z" fill="var(--red)"/>
    <path d="M0 82 C250 118 560 80 819 46 L819 54 C560 90 250 120 0 92 Z" fill="var(--white)"/>
  </svg>

  <div class="abs brand-badge" aria-label="Kestrel Baseball">
    <span class="name">Kestrel</span>
    <span class="sub">BASEBALL</span>
  </div>

  <div class="abs sport">SOFTBALL</div>
  <div class="abs summer">summer</div>
  <div class="abs camp">CAMP</div>
  <div class="abs year">2017</div>
  <div class="abs rule"></div>
  <div class="abs audience">for boys and girls</div>

  <svg class="abs swoosh" style="top:716px" width="819" height="160" viewBox="0 0 819 160" aria-hidden="true">
    <path d="M0 112 C400 112 600 62 819 22 L819 160 L0 160 Z" fill="var(--white)"/>
    <path d="M0 96 C400 96 600 46 819 0 L819 22 C600 62 400 112 0 112 Z" fill="var(--red)"/>
    <path d="M330 160 C480 120 650 90 819 80 L819 100 C660 110 500 135 400 160 Z" fill="var(--red)" opacity=".9"/>
  </svg>

  <div class="abs weeks-label">Weeks of</div>
  <ul class="abs dates">
    <li>JULY 10TH - 14TH</li>
    <li>JULY 17TH - 21ST.</li>
  </ul>

  <svg class="abs ages-icon" width="40" height="40" viewBox="0 0 40 40" aria-hidden="true">
    <circle cx="11" cy="7" r="5" fill="var(--red)"/><rect x="5" y="14" width="12" height="24" rx="3" fill="var(--red)"/>
    <circle cx="29" cy="7" r="5" fill="var(--red)"/><path d="M23 14h12l3 14h-6v10h-6V28h-6z" fill="var(--red)"/>
  </svg>
  <div class="abs ages-label">PLAYERS<br>AGES</div>
  <div class="abs ages-range">5 - 11</div>

  <div class="abs schedule">
    <div class="row">
      <svg width="36" height="36" viewBox="0 0 36 36" aria-hidden="true"><circle cx="18" cy="20" r="13" fill="none" stroke="var(--red)" stroke-width="4"/><path d="M18 13v8l5 3" stroke="var(--red)" stroke-width="3" fill="none"/><rect x="14" y="1" width="8" height="4" fill="var(--red)"/></svg>
      FULL DAY 9:30AM - 2:30PM
    </div>
    <div class="row indent">HALF DAY 9:30AM - 11:30AM</div>
  </div>

  <div class="abs cost-label">Cost:</div>
  <div class="abs cost-icon">$</div>
  <div class="abs prices">$295 / FULL DAY<br>$195/ HALF DAY</div>

  <div class="abs info-bar"></div>
  <p class="abs hosted">Hosted by "Kestrel Baseball" affiliated with the Harbor Comets Travel Baseball &amp; Softball Club and the Maple Ridge Youth League</p>
  <div class="abs partners">
    <span class="partner"><i></i>Comets</span>
    <span class="partner alt"><i></i>Maple Ridge</span>
  </div>

  <div class="abs location">
    <div class="block-title">
      <svg width="18" height="24" viewBox="0 0 18 24" aria-hidden="true"><path d="M9 0a9 9 0 0 1 9 9c0 7-9 15-9 15S0 16 0 9a9 9 0 0 1 9-9z" fill="var(--navy)"/><circle cx="9" cy="9" r="3.5" fill="var(--white)"/></svg>
      Camp Location:
    </div>
    <div class="block-text">MRYL, Route 9C<br>Birch Hollow.</div>
  </div>

  <div class="abs contact">
    <div class="block-title">
      <svg width="16" height="24" viewBox="0 0 16 24" aria-hidden="true"><rect x="0" y="0" width="16" height="24" rx="3" fill="var(--navy)"/><rect x="3" y="3" width="10" height="14" fill="var(--white)"/><circle cx="8" cy="20.5" r="1.6" fill="var(--white)"/></svg>
      Contact:
    </div>
    <div class="block-text">Phone 555-240-7813<br>Email <span class="lower">info@kestrelball.example</span></div>
  </div>
</main>
</body>
</html>
```